The BRV Relational Philanthropy Cycle

The title for this graphic is above. It must be included.
I am looking for a graphic representation of the relationship between the Christian school and the donor / pointing to the child (student) - the school's mission / outcome of investment through a gift / appreciation of the gift / communication of the gift impact for the child / stronger relationship going back to the child. This is not easy to do. I've tried to do it on my own and can't get it.
Any cliched child representations will be dismissed out of hand e.g. mortar boards, pencils, uniforms etc. The child should be abstract so that gender and race are irrelevant.
The key to this whole thing is the idea of RELATIONSHIP. The close relationship of donor and the Christian school, the pointing of that relationship to focus on the child / the school's mission, the outpouring of generosity that then happens in the heart of the donor and the gift that results, followed up by intentional work by the Christian school to thank and inform the donor - thank for the gift inform about the gift's expenditure and impact in the life of the child - all of which leads to a strengthening of the relationship and continued philanthropy as a never ending cycle.
It must be branded - logo and colors attached.
It must be obvious - easy to grasp the basic idea of relationship resulting in generosity / philanthropy. The visual should be clear - any words used illustrate - I should not 'need' the words to understand the idea.
I need it on a PP slide, jpeg, thumbnail. It must be highly legible in no more than 1/3 of a regular size piece of paper.
Our website is faithacademyworks.example
google donor cultivation cycle or donor giving cycle to see many examples of cycles that are used in secular contexts - the big difference in BRV's is the focus on the child and the importance of the relationship.

```html
<!DOCTYPE html>
<html lang="en">
<head>
<meta charset="utf-8">
<title>The BRV Relational Philanthropy Cycle</title>
<link rel="stylesheet" href="https://fonts.googleapis.com/css2?family=EB+Garamond:wght@500;600&family=Montserrat:wght@500;600;700&display=swap">
<style>
  :root {
    --brand-blue: #4372a8;
    --title-blue: #4a78ad;
    --title-grey: #6b6c6f;
    --ring-grey: #d9d9d9;
    --arrow-grey: #8e8e8e;
    --ink: #1f1f1f;
    --white: #ffffff;
    --page: #ffffff;
  }
  * { margin: 0; padding: 0; box-sizing: border-box; }
  html, body {
    width: 1200px;
    height: 871px;
    overflow: hidden;
    background: var(--page);
  }
  .canvas {
    position: relative;
    width: 1200px;
    height: 871px;
    background: var(--page);
  }
  .title {
    position: absolute;
    left: 90px;
    top: 74px;
    font-family: "EB Garamond", Georgia, serif;
    font-weight: 600;
    font-size: 36px;
    letter-spacing: -0.2px;
    color: var(--title-grey);
  }
  .title .title-brand { color: var(--title-blue); }
  .brand-name {
    position: absolute;
    left: 968px;
    top: 72px;
    font-family: "Montserrat", Arial, sans-serif;
    font-weight: 600;
    font-size: 44px;
    letter-spacing: 1px;
    color: var(--brand-blue);
  }
  .cycle {
    position: absolute;
    left: 0;
    top: 0;
  }
  .cycle-arrow { fill: none; stroke: var(--arrow-grey); stroke-width: 30; }
  .cycle-arrow-head { fill: var(--arrow-grey); }
  .outer-label {
    font-family: "Montserrat", Arial, sans-serif;
    font-weight: 500;
    font-size: 21px;
    letter-spacing: 0.6px;
    fill: var(--title-blue);
  }
  .inner-ring { fill: var(--ring-grey); }
  .inner-label {
    font-family: "Montserrat", Arial, sans-serif;
    font-weight: 500;
    font-size: 20px;
    letter-spacing: 0.4px;
    fill: var(--ink);
  }
  .inner-label .marker { fill: var(--brand-blue); font-size: 13px; }
  .node { fill: var(--brand-blue); stroke: var(--white); stroke-width: 3; }
  .link-line { stroke: var(--white); stroke-width: 2; }
  .icon { fill: none; stroke: var(--white); stroke-width: 2; stroke-linecap: round; stroke-linejoin: round; }
  .node-label {
    font-family: "Montserrat", Arial, sans-serif;
    font-weight: 700;
    font-size: 18px;
    fill: var(--white);
    text-anchor: middle;
  }
</style>
</head>
<body>
<main class="canvas">
  <h1 class="title"><span class="title-brand">The BRV</span> Relational Philanthropy Cycle</h1>
  <div class="brand-name">BRV</div>

  <svg class="cycle" width="1200" height="871" viewBox="0 0 1200 871" aria-label="Relational philanthropy cycle: donor, the child and good steward">
    <defs>
      <path id="outer-top-text" d="M 326 430 A 272 272 0 0 1 866 430"/>
      <path id="outer-bottom-text" d="M 331 555.5 A 282 282 0 0 0 861 555.5"/>
      <path id="inner-top-text" d="M 474 459 A 122 122 0 0 1 718 459"/>
      <path id="inner-bottom-text" d="M 462 459 A 134 134 0 0 0 730 459"/>
    </defs>

    <!-- generosity arrow (top) -->
    <path class="cycle-arrow" d="M 390.8 340.5 A 237 237 0 0 1 772.1 300.4"/>
    <polygon class="cycle-arrow-head" points="746,324 798,276 808,351"/>

    <!-- impact arrow (bottom) -->
    <path class="cycle-arrow" d="M 797 584.6 A 237 237 0 0 1 414.4 611.3"/>
    <polygon class="cycle-arrow-head" points="441,595 388,635 384,567"/>

    <text class="outer-label"><textPath href="#outer-top-text" startOffset="50%" text-anchor="middle">Outpouring of Generosity</textPath></text>
    <text class="outer-label"><textPath href="#outer-bottom-text" startOffset="50%" text-anchor="middle">Impact on the Child</textPath></text>

    <!-- inner relationship ring -->
    <circle class="inner-ring" cx="596" cy="459" r="151"/>
    <text class="inner-label"><textPath href="#inner-top-text" startOffset="50%" text-anchor="middle"><tspan class="marker">◂▸</tspan>  Focus on the Child  <tspan class="marker">◂▸</tspan></textPath></text>
    <text class="inner-label"><textPath href="#inner-bottom-text" startOffset="50%" text-anchor="middle"><tspan class="marker">◂▸</tspan>  Mission Delivery  <tspan class="marker">◂▸</tspan></textPath></text>

    <!-- nodes -->
    <circle class="node" cx="386" cy="459" r="94"/>
    <circle class="node" cx="806" cy="459" r="94"/>
    <circle class="node" cx="596" cy="459" r="94"/>

    <line class="link-line" x1="420" y1="461" x2="568" y2="461"/>
    <line class="link-line" x1="624" y1="461" x2="772" y2="461"/>

    <!-- donor icon: heart over open hand -->
    <g class="icon">
      <path d="M 388 433 C 378 425 372 418 375 411 C 378 404 386 405 388 411 C 390 405 398 404 401 411 C 404 418 398 425 388 433 Z"/>
      <path d="M 366 440 L 374 440 C 380 440 385 446 392 446 L 400 446 C 403 446 403 450 400 450 L 386 450"/>
      <path d="M 374 453 L 392 456 C 398 456 406 448 412 443 C 415 441 418 444 416 447 C 410 454 400 463 393 463 L 372 460"/>
      <path d="M 360 438 L 368 438 L 368 462 L 360 462"/>
    </g>

    <!-- child icon: three abstract figures -->
    <g class="icon">
      <circle cx="596" cy="414" r="6"/>
      <rect x="589" y="424" width="14" height="35" rx="7"/>
      <circle cx="577" cy="422" r="5"/>
      <rect x="571" y="430" width="12" height="29" rx="6"/>
      <circle cx="615" cy="422" r="5"/>
      <rect x="609" y="430" width="12" height="29" rx="6"/>
    </g>

    <!-- steward icon: sprout over open hand -->
    <g class="icon">
      <path d="M 800 444 L 800 414"/>
      <path d="M 800 426 C 790 426 784 420 784 410 C 794 410 800 416 800 426 Z"/>
      <path d="M 800 420 C 810 420 816 413 816 404 C 806 404 800 411 800 420 Z"/>
      <path d="M 800 434 C 792 434 788 430 788 423 C 795 423 800 427 800 434 Z"/>
      <path d="M 778 440 L 786 440 C 792 440 797 446 804 446 L 812 446 C 815 446 815 450 812 450 L 798 450"/>
      <path d="M 786 453 L 804 456 C 810 456 818 448 824 443 C 827 441 830 444 828 447 C 822 454 812 463 805 463 L 784 460"/>
      <path d="M 772 438 L 780 438 L 780 462 L 772 462"/>
    </g>

    <text class="node-label" x="388" y="497">DONOR</text>
    <text class="node-label" x="596" y="497">THE CHILD</text>
    <text class="node-label" x="806" y="485">GOOD</text>
    <text class="node-label" x="806" y="509">STEWARD</text>
  </svg>
</main>
</body>
</html>
```